Parcelwise HQ letterhead and envelope

Design a formal (8.5x11) letterhead and envelope for sales outreach and legal matters. Using design input from https://www.parcelwisehq.example/ and the attached documents.

Industry/Entity Type

Software Service

Requirements
Must have
• These 4 hex colors are our official colors:
• #355c98 [blue]
• #1eb1a2 [teal]
• #fdba12 [gold]
• #f1653b [orange]
• So no other colors besides these should be used.

```html
<!DOCTYPE html>
<html lang="en">
<head>
<meta charset="utf-8">
<title>Parcelwise HQ — Letterhead and Envelope</title>
<link rel="stylesheet" href="https://fonts.googleapis.com/css2?family=Open+Sans:wght@300;400;600&family=Roboto:wght@400&display=swap">
<style>
  :root {
    --brand-blue: #355c98;
    --paper: #efefef;
    --stage: #e3e3e3;
    --ink-dark: #3a3a3a;
    --ink-mid: #6e6e6e;
    --ink-light: #8a8a8a;
    --rule: #b9b9b9;
  }
  * { margin: 0; padding: 0; box-sizing: border-box; }
  html, body { width: 1200px; height: 946px; overflow: hidden; }
  body {
    background: var(--stage);
    font-family: "Open Sans", Arial, sans-serif;
    position: relative;
  }
  .sheet { position: absolute; background: var(--paper); }

  /* Shared brand lockup */
  .brand {
    position: absolute; display: flex; align-items: center; gap: 6px;
    color: var(--brand-blue); font-weight: 300; white-space: nowrap;
  }
  .brand-dot {
    border: 2px solid var(--brand-blue); border-radius: 50%; flex: none;
  }

  /* Letterhead */
  .letterhead { left: 107px; top: 148px; width: 478px; height: 672px; }
  .letterhead .brand { left: 30px; top: 45px; font-size: 22px; }
  .letterhead .brand-dot { width: 36px; height: 36px; }
  .header-contact {
    position: absolute; top: 49px; font-size: 7.5px; line-height: 11.2px;
    white-space: nowrap;
  }
  .header-contact.direct { left: 240px; color: var(--ink-dark); font-weight: 600; }
  .header-contact.office { left: 366px; color: var(--ink-light); }
  .header-rule {
    position: absolute; left: 356px; top: 48px; width: 1px; height: 30px;
    background: var(--rule);
  }
  .letter-body {
    position: absolute; left: 43px; width: 396px;
    font-family: "Roboto", Arial, sans-serif;
    font-size: 8.8px; line-height: 12.5px; color: var(--ink-mid);
  }
  .recipient { top: 198px; }
  .para-one { top: 273px; text-align: justify; }
  .para-two { top: 385px; text-align: justify; }
  .signature {
    position: absolute; left: 42px; top: 460px; width: 92px; height: 58px;
    background: linear-gradient(90deg, #e4e4e4, #ebebeb);
  }
  .signer-title { top: 529px; }

  /* Envelope back */
  .envelope-back { left: 630px; top: 314px; width: 475px; height: 237px; }
  .flap { position: absolute; left: 0; top: 0; }
  .flap-dot {
    position: absolute; left: 219px; top: 17px; width: 36px; height: 36px;
    border: 2px solid var(--paper); border-radius: 50%;
  }

  /* Envelope front */
  .envelope-front { left: 629px; top: 584px; width: 476px; height: 237px; }
  .envelope-front .brand { left: 23px; top: 30px; font-size: 16px; gap: 5px; }
  .envelope-front .brand-dot { width: 26px; height: 26px; }
  .return-address {
    position: absolute; left: 25px; font-size: 7px; line-height: 10.4px;
    white-space: nowrap;
  }
  .return-address.direct { top: 81px; color: var(--ink-dark); font-weight: 600; }
  .return-address.office { top: 118px; color: var(--ink-light); }
</style>
</head>
<body>

<section class="sheet letterhead" aria-label="Letterhead">
  <div class="brand"><span class="brand-dot"></span>Parcelwise HQ</div>
  <div class="header-contact direct">
    (555) 014-2290<br>mr@parcelwisehq.example<br>www.parcelwisehq.example
  </div>
  <div class="header-rule"></div>
  <div class="header-contact office">
    Main: (555) 019-4410<br>82 Linden Crossing<br>Fairbrook, OH 45000
  </div>

  <p class="letter-body recipient">Dear Alder<br>Northgate Print Works<br>Department Design</p>
  <p class="letter-body para-one">Lorem ipsum dolor sit amet, consectetuer adipiscing elit. Aenean commodo ligula eget dolor. Aenean massa. Cum sociis natoque penatibus et magnis dis parturient montes, nascetur ridiculus mus. Donec quam felis, ultricies nec, pellentesque eu, pretium quis, sem. Nulla consequat massa quis enim. Donec pede justo, fringilla vel, aliquet nec, vulputate eget, arcu. In enim justo, rhoncus ut, imperdiet a, venenatis vitae, justo. Nullam dictum felis eu pede mollis pretium. Integer tincidunt. Cras dapibus. Vivamus elementum semper nisi.Nullam dictum felis eu pede mollis pretium. Integer tincidunt. Cras dapibus. Vivamus elementum semper nisi.felis eu pede mollis pretium. Integer tincidunt. Cras dapibus.</p>
  <p class="letter-body para-two">Quisque rutrum. Aenean imperdiet. Etiam ultricies nisi vel augue. Curabitur ullamcorper ultricies nisi. Nam eget dui. Etiam rhoncus. Maecenas tempus, tellus eget condimentum rhoncus, sem quam semper libero, sit amet adipiscing sem neque sed ipsum.felis pede mollis pretium. I am tincidunt. Cras dapibus.</p>
  <div class="signature" role="img" aria-label="Handwritten signature of the director"></div>
  <p class="letter-body signer-title">Director/Excecutive Director</p>
</section>

<section class="sheet envelope-back" aria-label="Envelope back">
  <svg class="flap" width="475" height="72" viewBox="0 0 475 72" aria-hidden="true">
    <path d="M0 0 H475 L468 58 Q466 70 454 70 H21 Q9 70 7 58 Z" fill="var(--brand-blue)"/>
  </svg>
  <span class="flap-dot"></span>
</section>

<section class="sheet envelope-front" aria-label="Envelope front">
  <div class="brand"><span class="brand-dot"></span>Parcelwise HQ</div>
  <div class="return-address direct">
    (555) 014-2290<br>mr@parcelwisehq.example<br>parcelwisehq.example
  </div>
  <div class="return-address office">
    Main: (555) 019-4410<br>82 Linden Crossing<br>Fairbrook, OH 45000
  </div>
</section>

</body>
</html>
```